Road Construction Company needs business cards

We would like a new business card designed for our business.

We're a road construction company based in Qld, Australia.

Can the business card please have the following information on it.

Name: Warren Halbeck
Position: General Manager
Phone: 0472 915 348
Email: Warren.halbeck@tovrin.com.au
Address: 87 Marrow Ave, Pendlebay, QLD, 4023
Website: www.tovrin.com.au

Visually we'd like the card to be professional and simple.

Attached is our logo.

Our website is www.tovrin.com.au

Target Market(s)

Men aged 25-60

Contact Information for Business Card

As listed in project description

Font styles to use
Serif

Requirements
Must have
• Large logo on back of card

```html
<!DOCTYPE html>
<html lang="en">
<head>
<meta charset="utf-8">
<title>Tovrin business card</title>
<link rel="stylesheet" href="https://fonts.googleapis.com/css2?family=Poppins:wght@300;400;600;800&display=swap">
<style>
  :root {
    --backdrop: #434343;
    --paper: #ffffff;
    --blue-deep: #1b5cab;
    --blue-mid: #1f67b8;
    --blue-light: #3ba7da;
    --navy: #14213f;
    --ink: #3a3a3a;
  }
  * { margin: 0; padding: 0; box-sizing: border-box; }
  html, body { width: 1200px; height: 801px; overflow: hidden; }
  body {
    background: var(--backdrop);
    font-family: "Poppins", sans-serif;
    display: flex;
    align-items: center;
    justify-content: center;
    gap: 40px;
  }
  .card {
    position: relative;
    width: 540px;
    height: 309px;
    overflow: hidden;
    box-shadow: 0 14px 30px rgba(0,0,0,0.35);
  }
  .card-front { background: var(--paper); }
  .front-shapes { position: absolute; inset: 0; width: 100%; height: 100%; }
  .front-content {
    position: absolute;
    left: 268px;
    top: 34px;
    right: 20px;
  }
  .brand-name {
    font-weight: 800;
    font-size: 34px;
    letter-spacing: 1px;
    color: var(--blue-deep);
    line-height: 1;
  }
  .person-name {
    margin-top: 22px;
    font-weight: 600;
    font-size: 21px;
    color: var(--blue-deep);
    line-height: 1.1;
  }
  .person-role {
    font-weight: 300;
    font-size: 16px;
    color: var(--blue-light);
    line-height: 1.3;
  }
  .divider {
    width: 26px;
    height: 2px;
    background: var(--blue-light);
    margin: 10px 0 10px;
  }
  .address, .contact-list {
    font-size: 11.5px;
    color: var(--ink);
    line-height: 1.5;
  }
  .contact-list { list-style: none; }
  .contact-list li { display: flex; align-items: center; gap: 7px; }
  .contact-icon { width: 10px; height: 10px; fill: var(--blue-deep); flex: none; }
  .card-back {
    background: radial-gradient(ellipse at 25% 85%, #0b4fa0 0%, #123a78 40%, var(--navy) 100%);
  }
  .back-photo {
    position: absolute;
    inset: 0;
    background: radial-gradient(ellipse at 80% 30%, rgba(60,90,110,0.35) 0%, rgba(20,33,63,0) 60%);
  }
  .back-logo {
    position: absolute;
    inset: 0;
    display: flex;
    align-items: center;
    justify-content: center;
    font-weight: 800;
    font-size: 64px;
    letter-spacing: 3px;
    color: var(--paper);
  }
</style>
</head>
<body>
  <section class="card card-front">
    <svg class="front-shapes" viewBox="0 0 540 309" preserveAspectRatio="none" aria-hidden="true">
      <polygon fill="var(--blue-mid)" points="0,0 124,0 297,309 0,309"/>
      <polygon fill="var(--blue-light)" points="92,0 124,0 219,170 54,309"/>
      <polygon fill="var(--blue-deep)" points="0,0 92,0 54,309 0,309"/>
    </svg>
    <div class="front-content">
      <div class="brand-name">TOVRIN</div>
      <h1 class="person-name">Warren Halbeck</h1>
      <p class="person-role">General Manager</p>
      <div class="divider"></div>
      <p class="address">87 Marrow Ave,<br>Pendlebay, QLD, 4023</p>
      <ul class="contact-list">
        <li>
          <svg class="contact-icon" viewBox="0 0 10 10"><path d="M2 0.5 L3.8 2.6 L2.9 3.6 C3.5 4.9 5 6.4 6.4 7.1 L7.4 6.2 L9.5 8 L8.3 9.5 C4.5 9.2 0.8 5.5 0.5 1.7 Z"/></svg>
          0472 915 348
        </li>
        <li>
          <svg class="contact-icon" viewBox="0 0 10 10"><path d="M0.5 2 H9.5 V8.5 H0.5 Z M1 2.4 L5 5.5 L9 2.4" stroke="#fff" stroke-width="0.8"/></svg>
          Warren.halbeck@tovrin.com.au
        </li>
        <li>
          <svg class="contact-icon" viewBox="0 0 10 10"><circle cx="5" cy="5" r="4.5"/><path d="M0.5 5 H9.5 M5 0.5 C3 3 3 7 5 9.5 M5 0.5 C7 3 7 7 5 9.5" stroke="#fff" stroke-width="0.6" fill="none"/></svg>
          www.tovrin.com.au
        </li>
      </ul>
    </div>
  </section>

  <section class="card card-back">
    <div class="back-photo" role="img" aria-label="Road roller compacting fresh asphalt, tinted deep blue"></div>
    <div class="back-logo">TOVRIN</div>
  </section>
</body>
</html>
```